TuneRoost - Music Industry App needs a top quality wordpress homepage

We need a modern responsive wordpress homepage built. Our website will only feature one page with the goal to get people to sign up to our app. A word document has been uploaded outlining the page content/sections.

Once the homepage is finalised, I will also need 2 landing pages built as part of this competition. It will be very similar to the homepage with the same layout etc but just feature different images and content. The homepage is for anyone (artists and venues) to find out about us but the landing pages will be artist or venue specific.

The completed work must be delivered as an exportable file into wordpress and be designed properly so no more work is needed to begin utilising as the actual website. The images used must be setup correctly for speed and quality also.

Target Market(s)

Venues and Artists.

Coding

Coded - Design and coding required

Requirements
Must have
• UPDATE: High Res Logo files attached
• Must be a modern looking website and be responsive. Must look good across all devices from desktop, to mobile and tablet. Needs to be very high quality.
• Please see the attached logo - I am waiting for the final high quality version and will reupload when complete but this will be enough to get you started for now. The website must have a dark base colour and have red/white elements to match the logo. The red colour used MUST match the red colour used in the logo.
• Please have a go at creating it how you think is best and provide feedback from there. I am leaving it very open to the designers so I can get the best website possible and lots of different ideas etc.

```html
<!DOCTYPE html>
<html lang="en">
<head>
<meta charset="utf-8">
<title>TuneRoost – Homepage, desktop and mobile</title>
<link rel="stylesheet" href="https://fonts.googleapis.com/css2?family=Montserrat:ital,wght@0,400;0,500;0,600;0,700;1,400&family=Open+Sans:ital,wght@0,400;0,600;0,700;1,400&display=swap">
<style>
:root{
  --red:#d0021b;
  --red-deep:#7a0010;
  --black:#050505;
  --dark:#1c1c1c;
  --dark-2:#262626;
  --circle:#2b2b2b;
  --light:#f2f0f1;
  --paper:#ffffff;
  --muted:#bdbdbd;
  --ink:#222222;
  --ink-soft:#555555;
  --stage:#ececec;
  --head:'Montserrat',sans-serif;
  --body:'Open Sans',sans-serif;
}
*{box-sizing:border-box;margin:0;padding:0}
html,body{width:1200px;height:3052px;overflow:hidden}
body{background:var(--stage);font-family:var(--body);color:var(--ink);position:relative}
.page{position:absolute;overflow:hidden;background:var(--black)}
.page--desktop{left:65px;top:44px;width:788px;height:2447px}
.page--mobile{left:928px;top:53px;width:215px;height:2891px}
section,footer{position:relative;width:100%;overflow:hidden}
.photo{position:absolute;inset:0}
.layer{position:relative;height:100%}
h1,h2,h3{font-family:var(--head);font-weight:400}
.center{text-align:center}

/* brand */
.brand{display:flex;align-items:center;justify-content:center;gap:8px}
.brand__dot{width:22px;height:22px;border-radius:50%;background:var(--red)}
.brand__name{font-family:var(--head);font-weight:500;color:#fff;font-size:30px;letter-spacing:.5px}

/* hero */
.hero__photo{background:
  radial-gradient(ellipse at 50% 30%,#c8101c 0%,#9a0612 40%,transparent 75%),
  linear-gradient(180deg,#6e0009 0%,#b10614 45%,#5a0008 78%,var(--black) 100%)}
.hero__title{color:#fff;white-space:nowrap}
.hero__sub{color:#fff;font-family:var(--head)}
.hero__cta{color:#fff;font-family:var(--head);font-weight:500}
.signup{display:flex;background:#fff;border:3px solid #fff;margin:0 auto}
.signup__field{flex:1;display:flex;align-items:center;color:#666;font-family:var(--body)}
.signup__btn{background:var(--red);color:#fff;display:flex;align-items:center;justify-content:center;font-family:var(--head);font-weight:500}

/* steps */
.steps{background:var(--black);color:#fff}
.step{text-align:center}
.step__icon{border-radius:50%;background:var(--circle);display:flex;align-items:center;justify-content:center;margin:0 auto}
.step__num{font-family:var(--head);color:#fff}
.step__text{color:var(--muted);font-family:var(--body)}
.ic{fill:none;stroke:var(--red);stroke-width:1.6;stroke-linecap:round;stroke-linejoin:round}
.ic-fill{fill:var(--red);stroke:none}

/* why */
.why{background:var(--light)}
.why__title{color:var(--ink)}
.card{background:var(--paper);text-align:center}
.card__rule{width:14px;height:1px;background:var(--red);margin:0 auto}
.card__title{font-family:var(--body);font-weight:700;color:var(--ink)}
.card__text{color:var(--ink-soft)}

/* audiences */
.panel--dark{background:linear-gradient(180deg,#151515,#232323);color:#fff}
.panel--light{background:linear-gradient(180deg,#cfd0d4 0%,#b9bbc1 60%,#c9cace 100%);color:var(--ink)}
.ticks{list-style:none}
.ticks li{position:relative}
.ticks li::before{content:"";position:absolute;left:0;border-right:1.5px solid currentColor;border-bottom:1.5px solid currentColor;transform:rotate(-45deg)}
.ticks--red li::before{border-color:var(--red)}
.note{color:#ddd}

/* testimonials */
.testimonials__photo{background:linear-gradient(180deg,#f6f6f7 0%,#e3e4ea 55%,#9a97b0 85%,#3b2f4f 100%)}
.quote{background:#fff;border:1px solid #d8d8d8;box-shadow:0 2px 6px rgba(0,0,0,.12)}
.quote__avatar{background:linear-gradient(160deg,#b8b1aa,#6d6660)}
.quote__mark{color:var(--red);font-family:Georgia,serif;font-style:italic;font-weight:700}
.quote__text{font-style:italic;color:#333}
.quote__rule{height:1px;background:var(--red)}
.quote__by{color:var(--red);font-weight:700;font-family:var(--body)}
.dots{display:flex;justify-content:center;gap:5px}
.dots span{border-radius:50%;border:1px solid #333}
.dots span.on{background:#333}

/* about */
.about__photo{background:radial-gradient(ellipse at 55% 20%,#5b4a7a 0%,#3a2c4c 35%,#1c1620 70%,#121014 100%)}
.about__title{color:#fff}
.about__text{color:#e2e2e2}

/* contact */
.contact{background:var(--dark-2);color:#fff}
.field{border-bottom:1px solid #8a8a8a;color:#ddd}
.btn{background:var(--red);color:#fff;display:flex;align-items:center;justify-content:center;font-family:var(--body)}
.map{background:linear-gradient(135deg,#ecebe8,#e2e1dd)}
.map__card{position:absolute;background:#fff;box-shadow:0 1px 4px rgba(0,0,0,.25);text-align:center;color:#222}

/* footer */
.site-footer{background:var(--black);color:#ddd;text-align:center}

/* ============ desktop ============ */
.d-hero{height:454px}
.d-hero .brand{position:absolute;top:62px;left:0;right:0}
.d-hero .hero__title{position:absolute;top:172px;width:100%;font-size:32px}
.d-hero .hero__sub{position:absolute;top:222px;left:194px;width:400px;font-size:19px;line-height:24px}
.d-hero .hero__cta{position:absolute;top:286px;width:100%;font-size:15px}
.d-hero .signup{position:absolute;top:314px;left:231px;width:328px;height:33px}
.d-hero .signup__field{padding-left:12px;font-size:10px}
.d-hero .signup__btn{width:96px;font-size:12px}

.d-steps{height:355px}
.d-steps h2{position:absolute;top:68px;width:100%;font-size:20px}
.d-steps .row{position:absolute;top:110px;left:0;width:100%}
.d-steps .step{position:absolute;width:118px}
.d-steps .step__icon{width:62px;height:62px}
.d-steps .step__num{font-size:21px;margin-top:13px}
.d-steps .step__text{font-size:9.5px;line-height:15px;margin:4px 6px 0}

.d-why{height:332px}
.d-why h2{position:absolute;top:52px;width:100%;font-size:20px}
.d-why .card{position:absolute;top:90px;width:148px;height:188px;padding-top:22px}
.d-why .card svg{width:52px;height:52px}
.d-why .card__rule{margin-top:12px}
.d-why .card__title{font-size:11.5px;margin-top:11px}
.d-why .card__text{font-size:9px;line-height:13px;margin:8px 14px 0}

.d-aud{height:359px;display:flex}
.d-aud .panel{position:relative;height:100%}
.d-aud .panel--dark{width:392px;padding:38px 30px 0 106px}
.d-aud .panel--light{flex:1;padding:45px 80px 0 40px}
.d-aud h3{font-size:17px;margin-bottom:12px}
.d-aud .ticks li{font-size:10.3px;line-height:10.5px;padding-left:14px;margin-bottom:13px}
.d-aud .panel--light .ticks li{line-height:12px;margin-bottom:11px}
.d-aud .ticks li::before{top:2px;width:5px;height:5px}
.d-aud .note{font-size:8.8px;line-height:12.5px;margin-top:4px}
.d-aud .lead{font-size:11px;margin-top:4px}
.d-aud .signup{margin:12px 0 0;height:27px;width:252px;border-width:3px}
.d-aud .signup__field{font-size:8px;padding-left:10px}
.d-aud .signup__btn{width:70px;font-size:9.5px}

.d-test{height:269px}
.d-test h2{position:absolute;top:34px;width:100%;font-size:22px}
.d-test .quote{position:absolute;top:70px;width:276px;height:136px;border-radius:14px;padding:22px 18px 0 18px;display:flex;gap:10px}
.d-test .quote__avatar{width:48px;height:48px;flex:none}
.d-test .quote__mark{font-size:24px;line-height:18px;flex:none}
.d-test .quote__text{font-size:9px;line-height:14px}
.d-test .quote__rule{width:22px;margin:8px 0 6px}
.d-test .quote__by{font-size:8.5px}
.d-test .dots{position:absolute;top:220px;width:100%}
.d-test .dots span{width:9px;height:9px}

.d-about{height:272px}
.d-about h2{position:absolute;top:62px;width:100%;font-size:27px}
.d-about .about__text{position:absolute;top:118px;left:148px;width:496px;font-size:9.3px;line-height:15.5px;text-align:center}

.d-contact{height:338px;display:flex}
.d-contact .form{width:392px;padding:42px 0 0 94px}
.d-contact h2{font-size:23px;margin-bottom:12px}
.d-contact .field{width:256px;font-size:10.5px;padding:5px 0 4px;margin-bottom:9px}
.d-contact .field--msg{height:40px}
.d-contact .btn{width:100px;height:27px;font-size:11.5px;margin-top:12px}
.d-contact .map{flex:1;position:relative}

.d-footer{height:68px;font-size:10px;line-height:68px}

/* ============ mobile ============ */
.m-hero{height:355px}
.m-hero .brand{position:absolute;top:58px;left:0;right:0;gap:5px}
.m-hero .brand__dot{width:13px;height:13px}
.m-hero .brand__name{font-size:19px}
.m-hero .hero__title{position:absolute;top:156px;width:100%;font-size:16px}
.m-hero .hero__sub{position:absolute;top:186px;width:100%;font-size:9.5px;line-height:13px}
.m-hero .hero__join{position:absolute;top:216px;width:100%;font-size:13px;color:#fff;font-family:var(--head);font-weight:500;padding-left:17px}
.m-hero .hero__cta{position:absolute;top:240px;width:100%;font-size:11px}
.m-hero .signup{position:absolute;top:270px;left:13px;width:189px;height:28px;border-width:2px}
.m-hero .signup__field{font-size:9.5px;padding-left:11px}
.m-hero .signup__btn{width:81px;font-size:10.5px}

.m-steps{height:445px}
.m-steps h2{position:absolute;top:23px;width:100%;font-size:14px}
.m-steps .step{position:absolute;width:92px}
.m-steps .step__icon{width:46px;height:46px}
.m-steps .step__icon svg{width:22px;height:22px}
.m-steps .step__num{font-size:15px;margin-top:8px}
.m-steps .step__text{font-size:7px;line-height:10.5px}

.m-why{height:308px}
.m-why h2{position:absolute;top:36px;width:100%;font-size:17px}
.m-why .card{position:absolute;top:78px;left:43px;width:135px;height:165px;padding-top:22px}
.m-why .card svg{width:46px;height:46px}
.m-why .card__rule{margin-top:12px}
.m-why .card__title{font-size:10.5px;margin-top:8px}
.m-why .card__text{font-size:8px;line-height:12px;margin:6px 18px 0}
.m-why .arrow{position:absolute;top:150px;width:12px;height:26px}

.m-aud{padding:38px 14px 0 20px}
.m-venues{height:353px}
.m-artists{height:331px;padding-top:16px}
.m-aud h3{font-size:16px;text-align:center;margin-bottom:12px}
.m-aud .ticks li{font-size:8.5px;line-height:8.5px;padding-left:11px;margin-bottom:10px}
.m-artists .ticks li{line-height:11px;margin-bottom:12px}
.m-aud .ticks li::before{top:2px;width:4px;height:4px}
.m-aud .note{font-size:7.3px;line-height:12.5px;margin-top:2px}
.m-aud .lead{font-size:9.5px;line-height:13px;text-align:center;margin-top:2px}
.m-aud .signup{margin:10px 0 0 0;width:180px;height:27px;border-width:2px}
.m-venues .signup{margin-left:-1px}
.m-artists .signup{margin-left:1px;border:1px solid #ddd}
.m-aud .signup__field{font-size:9px;padding-left:10px}
.m-aud .signup__btn{width:76px;font-size:9px}
.m-artists .signup__btn{width:60px;margin:3px}

.m-test{height:210px}
.m-test h2{position:absolute;top:18px;width:100%;font-size:16.5px}
.m-test .quote{position:absolute;top:44px;left:16px;width:186px;height:108px;border-radius:10px;padding:16px 10px 0 14px;display:flex;gap:8px}
.m-test .quote__avatar{width:38px;height:38px;flex:none}
.m-test .quote__mark{font-size:16px;line-height:12px;flex:none}
.m-test .quote__text{font-size:7.3px;line-height:11px}
.m-test .quote__rule{width:16px;margin:5px 0 4px}
.m-test .quote__by{font-size:6.8px}
.m-test .dots{position:absolute;top:164px;width:100%}
.m-test .dots span{width:7px;height:7px}

.m-about{height:288px}
.m-about h2{position:absolute;top:30px;width:100%;font-size:19px}
.m-about .about__text{position:absolute;top:73px;left:15px;width:185px;font-size:7.7px;line-height:15.2px;text-align:center}

.m-contact{height:275px;padding:24px 15px 0 28px}
.m-contact h2{font-size:19px;text-align:center;margin:0 0 12px -12px}
.m-contact .field{font-size:9px;padding:4px 0 6px;margin-bottom:8px}
.m-contact .field--msg{height:32px}
.m-contact .btn{width:95px;height:26px;font-size:10.5px;margin:14px 0 0 31px}
.m-map{height:263px}
.m-footer{height:63px;font-size:8.5px;line-height:12px;padding-top:16px}
</style>
</head>
<body>

<svg width="0" height="0" style="position:absolute" aria-hidden="true">
  <defs>
    <symbol id="i-form" viewBox="0 0 24 24"><rect class="ic" x="5" y="3" width="14" height="18" rx="1.5"/><path class="ic" d="M8 8h8M8 12h8M8 16h5"/></symbol>
    <symbol id="i-music" viewBox="0 0 24 24"><path class="ic-fill" d="M9 4l10-2v13.5a3 3 0 1 1-2-2.8V6.3l-6 1.2v10a3 3 0 1 1-2-2.8z"/></symbol>
    <symbol id="i-phone" viewBox="0 0 24 24"><circle class="ic" cx="12" cy="12" r="9"/><path class="ic" d="M8.5 7.5l2 2-1 1.5a6 6 0 0 0 3.5 3.5l1.5-1 2 2-1.5 1.5c-3.5 0-8-4.5-8-8z"/></symbol>
    <symbol id="i-pay" viewBox="0 0 24 24"><circle class="ic" cx="15" cy="8" r="4.5"/><path class="ic" d="M15 6v4M3 15h5l3 1.5h5l-1 2H9M3 19h4l5 2 8-4"/></symbol>
    <symbol id="i-clock" viewBox="0 0 24 24"><circle class="ic" cx="13" cy="12" r="8"/><path class="ic" d="M13 7v5l3 2M2 10h4M3 13h3M2 16h4"/></symbol>
    <symbol id="w-simple" viewBox="0 0 48 48"><rect x="8" y="6" width="28" height="34" rx="2" fill="#fff" stroke="#444" stroke-width="1.5"/><rect x="8" y="6" width="28" height="6" fill="var(--red)"/><path d="M13 18h14M13 23h10M13 28h12" stroke="#777" stroke-width="1.5"/><circle cx="32" cy="32" r="7" fill="var(--red)"/><path d="M29 32l2.2 2.2L35.5 30" stroke="#fff" stroke-width="1.8" fill="none"/><path d="M37 36l5 6" stroke="#444" stroke-width="2"/></symbol>
    <symbol id="w-connect" viewBox="0 0 48 48"><path d="M4 14l10-4 10 6 10-6 10 4v14l-8 4-12 6-12-6-8-4z" fill="var(--red)"/><path d="M14 26l6 5M18 23l7 6M22 21l7 6" stroke="#fff" stroke-width="1.8"/></symbol>
    <symbol id="w-shield" viewBox="0 0 48 48"><circle cx="24" cy="24" r="21" fill="#e6e6e6"/><path d="M24 7l14 5v10c0 9-6 15-14 19-8-4-14-10-14-19V12z" fill="var(--red)"/><path d="M18 24l5 5 9-10" stroke="#fff" stroke-width="3" fill="none"/></symbol>
    <symbol id="w-price" viewBox="0 0 48 48"><circle cx="24" cy="24" r="21" fill="#e6e6e6"/><circle cx="28" cy="15" r="7" fill="var(--red)"/><text x="28" y="19" font-size="10" font-family="Open Sans,sans-serif" font-weight="700" fill="#fff" text-anchor="middle">$</text><path d="M8 33l8-6h10l-2 4h-7M8 38l10 0 14-8 5 2-12 10H10z" fill="var(--red)"/></symbol>
    <symbol id="i-pin" viewBox="0 0 24 32"><path d="M12 1a11 11 0 0 0-11 11c0 8 11 19 11 19s11-11 11-19A11 11 0 0 0 12 1z" fill="var(--red)"/><circle cx="12" cy="12" r="4" fill="#fff"/></symbol>
  </defs>
</svg>

<!-- ================= DESKTOP ================= -->
<main class="page page--desktop">

  <section class="hero d-hero center">
    <div class="photo hero__photo" role="img" aria-label="Concert crowd with raised hands under red stage lights"></div>
    <div class="layer">
      <div class="brand"><span class="brand__dot"></span><span class="brand__name">TuneRoost</span></div>
      <h1 class="hero__title">Hailora for Live Music</h1>
      <p class="hero__sub">TuneRoost connects venues with artists to make booking gigs simple</p>
      <p class="hero__cta">Join Now for FREE</p>
      <div class="signup"><span class="signup__field">Email address</span><span class="signup__btn">Join Now</span></div>
    </div>
  </section>

  <section class="steps d-steps center">
    <h2>How TuneRoost Works</h2>
    <div class="row">
      <div class="step" style="left:97px"><div class="step__icon"><svg width="30" height="30"><use href="#i-form"/></svg></div><div class="step__num">1</div><p class="step__text">Artists and venues sign up for free and create a profile</p></div>
      <div class="step" style="left:217px"><div class="step__icon"><svg width="30" height="30"><use href="#i-music"/></svg></div><div class="step__num">2</div><p class="step__text">Venues search for an artist for their upcoming gigs</p></div>
      <div class="step" style="left:336px"><div class="step__icon"><svg width="30" height="30"><use href="#i-phone"/></svg></div><div class="step__num">3</div><p class="step__text">Venues request a quote and communicate with the artist direct</p></div>
      <div class="step" style="left:454px"><div class="step__icon"><svg width="30" height="30"><use href="#i-pay"/></svg></div><div class="step__num">4</div><p class="step__text">The gig is booked in once payment is provided by the venue.</p></div>
      <div class="step" style="left:575px"><div class="step__icon"><svg width="30" height="30"><use href="#i-clock"/></svg></div><div class="step__num">5</div><p class="step__text">Upon completion the money is paid to the artist within 48 hours or less.</p></div>
    </div>
  </section>

  <section class="why d-why center">
    <h2 class="why__title">Why TuneRoost?</h2>
    <div class="card" style="left:77px"><svg><use href="#w-simple"/></svg><div class="card__rule"></div><h3 class="card__title">Simple</h3><p class="card__text">TuneRoost makes gig booking easy for both the venue and artist.</p></div>
    <div class="card" style="left:237px"><svg><use href="#w-connect"/></svg><div class="card__rule"></div><h3 class="card__title">Connect</h3><p class="card__text">Join the TuneRoost community which is full of amazing artists and venues.</p></div>
    <div class="card" style="left:397px"><svg><use href="#w-shield"/></svg><div class="card__rule"></div><h3 class="card__title">Protection</h3><p class="card__text">Everyone is protected with our complimentary dispute resolutions.</p></div>
    <div class="card" style="left:557px"><svg><use href="#w-price"/></svg><div class="card__rule"></div><h3 class="card__title">Price</h3><p class="card__text">Get the best rate possible with TuneRoost only receiving 5% of the artists fee.</p></div>
  </section>

  <section class="audiences d-aud">
    <div class="panel panel--dark" role="img" aria-label="Dark concert crowd photo behind the venue offer">
      <h3>Venues</h3>
      <ul class="ticks">
        <li>TuneRoost is a 100% FREE service for all venues - you pay us nothing!</li>
        <li>Get instant access to hundreds of artists around your local community</li>
        <li>All genres to suit any venue from a pub to a wedding or even a nightclub</li>
        <li>Simple booking process with a money back guarantee</li>
        <li>Communicate directly with the artist and negotiate the price</li>
      </ul>
      <p class="note">TuneRoost is not yet ready to host gigs as we're currently working on building our artists. We are launching for venues in Q4 2019. Pre-register now to keep informed and be one of the first people to use our platform.</p>
      <div class="signup"><span class="signup__field">Email address</span><span class="signup__btn">Pre-Register</span></div>
    </div>
    <div class="panel panel--light" role="img" aria-label="Pale grey concert crowd photo behind the artist offer">
      <h3>Artists</h3>
      <ul class="ticks ticks--red">
        <li>Sign up to TuneRoost for FREE and get yourself in front of venues</li>
        <li>Only pay us if you get a gig - we only get 10% of the fee you charge the venue</li>
        <li>All genres and artists welcome - as long as you're experienced and professional</li>
        <li>Get paid within 48 hours or less after the gig guaranteed!</li>
        <li>Negotiate your price and don't pay huge agent fees to ensure you earn top dollar</li>
      </ul>
      <p class="lead">Sign up and create your TuneRoost profile now</p>
      <div class="signup" style="border:1px solid #ddd"><span class="signup__field">Email address</span><span class="signup__btn" style="margin:3px;width:60px">Join Now</span></div>
    </div>
  </section>

  <section class="testimonials d-test center">
    <div class="photo testimonials__photo" role="img" aria-label="Faded concert crowd photo fading into purple stage light"></div>
    <div class="layer">
      <h2>Testimonials</h2>
      <article class="quote" style="left:110px">
        <div class="quote__avatar" role="img" aria-label="Portrait of the reviewer"></div>
        <span class="quote__mark">“</span>
        <div style="text-align:left"><p class="quote__text">Pellentesque faucibus Ut accumsan ultricies elit Maecenas at justo id velit placerat molestie Donec dictum lectus non odio Cras a ante vitae enim iaculis aliquam Mauris nunc quam</p><div class="quote__rule"></div><p class="quote__by">BY AUTHOR NAME</p></div>
      </article>
      <article class="quote" style="left:397px">
        <div class="quote__avatar" role="img" aria-label="Portrait of the reviewer"></div>
        <span class="quote__mark">“</span>
        <div style="text-align:left"><p class="quote__text">Pellentesque faucibus Ut accumsan ultricies elit Maecenas at justo id velit placerat molestie Donec dictum lectus non odio Cras a ante vitae enim iaculis aliquam Mauris nunc quam</p><div class="quote__rule"></div><p class="quote__by">BY AUTHOR NAME</p></div>
      </article>
      <div class="dots"><span></span><span class="on"></span><span></span></div>
    </div>
  </section>

  <section class="about d-about">
    <div class="photo about__photo" role="img" aria-label="Crowd silhouettes in front of a purple-lit stage"></div>
    <div class="layer">
      <h2 class="about__title center">About TuneRoost</h2>
      <p class="about__text">Lorem ipsum is a pseudo-Latin text used in web design, typography, layout, and printing in place of English to emphasise design elements over content. It's also called placeholder (or filler) text. It's a convenient tool for mock-ups. It helps to outline the visual elements of a document or presentation, eg typography, font, or layout. Lorem ipsum is mostly a part of a Latin text by the classical author and philosopher Varrenus. Its words and letters have been changed by addition or removal, so to deliberately render its content nonsensical; it's not genuine, correct</p>
    </div>
  </section>

  <section class="contact d-contact">
    <div class="form">
      <h2>Contact Us</h2>
      <div class="field">Name *</div>
      <div class="field">Company</div>
      <div class="field">E-mail *</div>
      <div class="field">Phone Number</div>
      <div class="field field--msg">Message</div>
      <div class="btn">Submit</div>
    </div>
    <div class="map" role="img" aria-label="Street map around the office location">
      <svg style="position:absolute;left:190px;top:118px" width="24" height="32"><use href="#i-pin"/></svg>
      <div class="map__card" style="left:130px;top:160px;width:150px;padding:10px 6px;font-size:10px;line-height:13px">Fernvale, Cobalt Ridge,<br>North Harlow</div>
    </div>
  </section>

  <footer class="site-footer d-footer">© 2019 TuneRoost &nbsp;All right reserved &nbsp;| &nbsp;Privacy Policy</footer>
</main>

<!-- ================= MOBILE ================= -->
<main class="page page--mobile">

  <section class="hero m-hero center">
    <div class="photo hero__photo" role="img" aria-label="Concert crowd with raised hands under red stage lights"></div>
    <div class="layer">
      <div class="brand"><span class="brand__dot"></span><span class="brand__name">TuneRoost</span></div>
      <h1 class="hero__title">Hailora for Live Music</h1>
      <p class="hero__sub">TuneRoost connects venues with<br>artists to make booking gigs simple</p>
      <p class="hero__join" style="text-align:left">Join Now for FREE</p>
      <p class="hero__cta">Join Now for FREE</p>
      <div class="signup"><span class="signup__field">Email address</span><span class="signup__btn">Join Now</span></div>
    </div>
  </section>

  <section class="steps m-steps center">
    <h2>How TuneRoost Works</h2>
    <div class="step" style="left:62px;top:55px"><div class="step__icon"><svg><use href="#i-form"/></svg></div><div class="step__num">1</div><p class="step__text">Artists and venues<br>sign up for free and<br>create a profile</p></div>
    <div class="step" style="left:14px;top:175px"><div class="step__icon"><svg><use href="#i-music"/></svg></div><div class="step__num">2</div><p class="step__text">Venues search for<br>an artist for their<br>upcoming gigs</p></div>
    <div class="step" style="left:110px;top:178px"><div class="step__icon"><svg><use href="#i-phone"/></svg></div><div class="step__num">3</div><p class="step__text">Venues request a<br>quote and communicate<br>with the artist direct</p></div>
    <div class="step" style="left:14px;top:300px"><div class="step__icon"><svg><use href="#i-pay"/></svg></div><div class="step__num">4</div><p class="step__text">The gig is booked in<br>once payment is<br>provided by the venue</p></div>
    <div class="step" style="left:110px;top:300px"><div class="step__icon"><svg><use href="#i-clock"/></svg></div><div class="step__num">5</div><p class="step__text">Upon completion the<br>money is paid to the artist<br>within 48 hours or less.</p></div>
  </section>

  <section class="why m-why center">
    <h2 class="why__title">Why TuneRoost?</h2>
    <svg class="arrow" style="left:12px" viewBox="0 0 12 26"><path d="M10 2L2 13l8 11" fill="none" stroke="#333" stroke-width="1.5"/></svg>
    <div class="card"><svg><use href="#w-simple"/></svg><div class="card__rule"></div><h3 class="card__title">Simple</h3><p class="card__text">TuneRoost makes gig booking easy for both the venue and artist.</p></div>
    <svg class="arrow" style="right:12px" viewBox="0 0 12 26"><path d="M2 2l8 11-8 11" fill="none" stroke="#333" stroke-width="1.5"/></svg>
  </section>

  <section class="audiences m-aud m-venues panel--dark" role="img" aria-label="Dark concert crowd photo behind the venue offer">
    <h3>Venues</h3>
    <ul class="ticks">
      <li>TuneRoost is a 100% FREE service for all venues - you pay us nothing!</li>
      <li>Get instant access to hundreds of artists around your local community</li>
      <li>All genres to suit any venue from a pub to a wedding or even a nightclub</li>
      <li>Simple booking process with a money back guarantee</li>
      <li>Communicate directly with the artist and negotiate the price</li>
    </ul>
    <p class="note">TuneRoost is not yet ready to host gigs as we're currently working on building our artists. We are launching for venues in Q4 2019. Pre-register now to keep informed and be one of the first people to use our platform.</p>
    <div class="signup"><span class="signup__field">Email address</span><span class="signup__btn">Pre-Register</span></div>
  </section>

  <section class="audiences m-aud m-artists panel--light" role="img" aria-label="Pale grey concert crowd photo behind the artist offer">
    <h3>Artists</h3>
    <ul class="ticks ticks--red">
      <li>Sign up to TuneRoost for FREE and get yourself in front of venues</li>
      <li>Only pay us if you get a gig - we only get 10% of the fee you charge the venue</li>
      <li>All genres and artists welcome - as long as you're experienced and professional</li>
      <li>Get paid within 48 hours or less after the gig guaranteed!</li>
      <li>Negotiate your price and don't pay huge agent fees to ensure you earn top dollar</li>
    </ul>
    <p class="lead">Sign up and create your<br>TuneRoost profile now</p>
    <div class="signup"><span class="signup__field">Email address</span><span class="signup__btn">Join Now</span></div>
  </section>

  <section class="testimonials m-test center">
    <div class="photo testimonials__photo" role="img" aria-label="Faded concert crowd photo fading into purple stage light"></div>
    <div class="layer">
      <h2>Testimonials</h2>
      <article class="quote">
        <div class="quote__avatar" role="img" aria-label="Portrait of the reviewer"></div>
        <span class="quote__mark">“</span>
        <div style="text-align:left"><p class="quote__text">Pellentesque faucibus Ut accumsan ultricies elit Maecenas at justo id velit placerat molestie Donec dictum lectus non odio</p><div class="quote__rule"></div><p class="quote__by">BY AUTHOR NAME</p></div>
      </article>
      <div class="dots"><span></span><span class="on"></span><span></span></div>
    </div>
  </section>

  <section class="about m-about">
    <div class="photo about__photo" role="img" aria-label="Crowd silhouettes in front of a purple-lit stage"></div>
    <div class="layer">
      <h2 class="about__title center">About TuneRoost</h2>
      <p class="about__text">Lorem ipsum is a pseudo-Latin text used in web design, typography, layout, and printing in place of English to emphasise design elements over content. It's also called placeholder (or filler) text. It's a convenient tool for mock-ups. It helps to outline the visual elements of a document or presentation, eg typography, font, or layout. Lorem ipsum is mostly a part of a Latin text by the classical author and philosopher Varrenus. Its words and letters have been changed by addition or removal, so to deliberately render its content nonsensical; it's not genuine, correct</p>
    </div>
  </section>

  <section class="contact m-contact">
    <h2>Contact Us</h2>
    <div class="field">Name *</div>
    <div class="field">Company</div>
    <div class="field">E-mail *</div>
    <div class="field">Phone Number</div>
    <div class="field field--msg">Message</div>
    <div class="btn">Submit</div>
  </section>

  <section class="map m-map" role="img" aria-label="Street map around the office location">
    <svg style="position:absolute;left:96px;top:88px" width="24" height="32"><use href="#i-pin"/></svg>
    <div class="map__card" style="left:40px;top:130px;width:138px;padding:9px 4px;font-size:8.5px;line-height:12px">Fernvale, Cobalt Ridge,<br>North Harlow</div>
  </section>

  <footer class="site-footer m-footer">© 2019 TuneRoost &nbsp;All right reserved<br>Privacy Policy</footer>
</main>

</body>
</html>
```